Business IT Services Billboard to attract local small businesses

We are Brivoqua, a premier Managed Service Provider (MSP) specializing in comprehensive IT services and VOIP phone solutions exclusively for businesses. Our goal is to create a dynamic and visually engaging billboard advertisement that not only highlights our cutting-edge IT solutions but also emphasizes our state-of-the-art VOIP phone services. This billboard should communicate our commitment to providing innovative, reliable, and holistic technology solutions.
See the attached supporting documentation.
Target Market(s)
small business
Industry/Entity Type
Information Technology
Colors
Designer to choose colors to be used in the design.
Look and feel
Each slider illustrates characteristics of the customer's brand and the style your logo design should communicate.

```html
<!DOCTYPE html>
<html lang="en">
<head>
<meta charset="utf-8">
<title>Brivoqua Billboard</title>
<link rel="stylesheet" href="https://fonts.googleapis.com/css2?family=Archivo+Black&family=Montserrat:wght@400;700&family=Oswald:wght@600&family=Poppins:wght@600&display=swap">
<style>
  :root {
    --canvas-grey: #9b9b9b;
    --navy: #0b2446;
    --navy-deep: #071a34;
    --brand-blue: #2a7fd0;
    --pill-blue: #1f74c4;
    --accent-orange: #e4560f;
    --ink: #161616;
    --white: #ffffff;
  }
  * { box-sizing: border-box; margin: 0; padding: 0; }
  html, body { width: 991px; height: 1200px; overflow: hidden; }
  body { background: var(--canvas-grey); position: relative; }

  .billboard {
    position: absolute; left: 20px; top: 461px;
    width: 951px; height: 278px;
    background: var(--white);
    box-shadow: 4px 6px 10px rgba(0,0,0,0.35);
    overflow: hidden;
  }
  .hero-band {
    position: absolute; left: 0; top: 0; width: 951px; height: 178px;
    background: radial-gradient(ellipse at 78% 20%, #1a3d6e 0%, var(--navy) 45%, var(--navy-deep) 100%);
  }
  .brand-name {
    position: absolute; left: 22px; top: 70px;
    font-family: "Archivo Black", sans-serif; font-size: 27px;
    color: var(--brand-blue); letter-spacing: 0.5px;
  }
  .headline {
    position: absolute; left: 212px; top: 14px;
    font-family: "Oswald", sans-serif; font-weight: 600; font-size: 48px;
    line-height: 1; color: var(--brand-blue); letter-spacing: -0.5px;
  }
  .subhead {
    position: absolute; left: 214px; top: 72px;
    font-family: "Montserrat", sans-serif; font-weight: 400; font-size: 32px;
    line-height: 1; color: var(--white); letter-spacing: 9.5px;
  }
  .audience-pill {
    position: absolute; left: 212px; top: 124px; width: 453px; height: 37px;
    background: var(--accent-orange); border: 1.5px solid #f3c7ab; border-radius: 18px;
    display: flex; align-items: center; justify-content: center;
    font-family: "Archivo Black", sans-serif; font-size: 24px;
    color: var(--white); letter-spacing: 2px;
  }
  .team-photo {
    position: absolute; left: 693px; top: 0; width: 258px; height: 205px;
    background: linear-gradient(160deg, #1c3a63 0%, #31465f 45%, #5b6470 80%, #8c9198 100%);
  }
  .tagline {
    position: absolute; left: 20px; top: 189px;
    font-family: "Poppins", sans-serif; font-weight: 600; font-size: 16.5px;
    color: var(--ink);
  }
  .cta {
    position: absolute; left: 20px; top: 228px;
    font-family: "Montserrat", sans-serif; font-size: 24px; color: var(--ink);
    white-space: nowrap;
  }
  .cta strong { color: var(--pill-blue); font-weight: 700; }
  .url-pill {
    position: absolute; left: 490px; top: 223px; width: 461px; height: 39px;
    background: var(--pill-blue); border-radius: 20px 0 0 20px;
    box-shadow: 0 3px 4px rgba(0,0,0,0.25);
    display: flex; align-items: center; padding-left: 26px;
    font-family: "Montserrat", sans-serif; font-size: 26px; color: var(--white);
    letter-spacing: 4px; white-space: nowrap;
  }
  .url-pill strong { font-weight: 700; }
</style>
</head>
<body>
  <div class="billboard">
    <div class="hero-band"></div>
    <div class="brand-name">BRIVOQUA</div>
    <div class="headline">SEAMLESS TECHNOLOGY</div>
    <div class="subhead">SOLUTIONS FOR</div>
    <div class="audience-pill">MODERN BUSINESSES</div>
    <div class="team-photo" role="img" aria-label="Two businessmen in suits giving a high five, one holding a laptop, with a desk VOIP phone in front"></div>
    <p class="tagline">Innovative IT and VOIP Solutions Tailored for Your Business Success</p>
    <p class="cta"><strong>TRANSFORM YOUR TECH</strong> TODAY AT</p>
    <div class="url-pill">www.<strong>brivoqua</strong>.com</div>
  </div>
</body>
</html>
```